NZ First of it's kind solutions directory and marketplace for busy Mums needs a business card design

We need a business card design for our new nationwide business in NZ (long term plans to go global). We provide solutions to the everyday challenges that busy Mums face by connecting them with quality communities and suppliers of carefully selected, relevant products and services. We sell direct via our online marketplace. The final design should communicate our values of inclusivity, quality and smart solutions. Colours should incorporate our logo colour palette of #477077 and #6ba8b2. Our website is at https://www.brightnestmums.example

Target Market(s)

busy Mums, Age 28 – 50, female, income over $100K, location main centres NZ primarily but NZ wide. Is likely juggling work or career with a young family. Probably had hobbies which have fallen by the wayside.
-Wants to succeed in her chosen career without compromising on family life
-to successfully juggle her career without feeling like she is compromising her children
- Is time poor, something always has to give and it’s generally her health (she’ll stay up late, get stressed)
- probably ex corporate or professional career. Has discretional income

Industry/Entity Type

Business

Contact Information for Business Card

Lena Forbisher, Founder, BrightNestMums.example (Strapline Tap; Gather; Sorted), 47 Kowhai Terrace, Ellerslie, Auckland 1051, New Zealand. Mob: 021 483 517 Ph: +64 (0)9 571 4860

Font styles to use
Other font styles liked:
• Raleway, and/or Architects Daughter

Colors
00a990
33b8a4
86cfc6
cfeae6

Requirements
Must have
• the above details, streamline. the logo and colours associated with those logos
Should not have
• foil or metallic colours

```html
<!DOCTYPE html>
<html lang="en">
<head>
<meta charset="utf-8">
<title>BrightNestMums – Business Card</title>
<link rel="stylesheet" href="https://fonts.googleapis.com/css2?family=Roboto:wght@400;500&family=Roboto+Condensed:wght@400&display=swap">
<style>
  :root {
    --brand-dark: #477077;
    --brand-light: #6ba8b2;
    --paper: #f2f2f2;
    --white: #ffffff;
    --backdrop: #262626;
  }
  * { box-sizing: border-box; margin: 0; padding: 0; }
  html, body { width: 1200px; height: 960px; overflow: hidden; }
  body {
    background: var(--backdrop);
    font-family: "Roboto", Arial, sans-serif;
    position: relative;
  }
  .card {
    position: absolute;
    width: 600px;
    height: 343px;
    overflow: hidden;
    box-shadow: 0 2px 4px rgba(0,0,0,0.5);
  }
  .card--front { left: 314px; top: 113px; background: var(--paper); }
  .card--back { left: 311px; top: 472px; background: var(--brand-light); }

  .front-sweep { position: absolute; inset: 0; width: 600px; height: 343px; }

  .wordmark {
    position: absolute;
    display: flex;
    align-items: center;
    gap: 12px;
    left: 52px;
    top: 74px;
  }
  .wordmark__dot {
    width: 34px; height: 34px; border-radius: 50%;
    background: var(--brand-dark);
  }
  .wordmark__name {
    font-size: 33px;
    font-weight: 500;
    color: var(--brand-dark);
    letter-spacing: -0.5px;
  }

  .contact {
    position: absolute;
    right: 23px;
    top: 163px;
    text-align: right;
    color: var(--white);
  }
  .contact__name {
    font-family: "Roboto Condensed", "Arial Narrow", sans-serif;
    font-size: 20px;
    color: var(--brand-light);
    text-transform: uppercase;
    line-height: 24px;
  }
  .contact__role {
    font-size: 15px;
    font-weight: 500;
    text-transform: uppercase;
    line-height: 20px;
    margin-bottom: 16px;
  }
  .contact__line {
    display: flex;
    justify-content: flex-end;
    align-items: center;
    gap: 6px;
    font-size: 14px;
    line-height: 19px;
  }
  .contact__icon { width: 14px; height: 14px; flex: none; }
  .contact__address { font-size: 14px; line-height: 18px; margin-top: 7px; }

  .back-mark {
    position: absolute;
    left: 0; right: 0; top: 130px;
    display: flex;
    justify-content: center;
    align-items: center;
    gap: 14px;
  }
  .back-mark__dot { width: 44px; height: 44px; border-radius: 50%; background: var(--white); }
  .back-mark__name { font-size: 40px; font-weight: 500; color: var(--white); }
  .strapline {
    position: absolute;
    left: 0; right: 0; top: 305px;
    text-align: center;
    font-size: 14px;
    color: var(--white);
  }
</style>
</head>
<body>
  <section class="card card--front">
    <svg class="front-sweep" viewBox="0 0 600 343" aria-hidden="true">
      <path fill="var(--brand-light)" d="M470,0 C500,30 480,120 362,196 C272,255 160,325 101,343 L600,343 L600,0 Z"/>
      <path fill="var(--white)" d="M478,0 C507,30 487,120 377,199 C292,258 205,320 153,343 L600,343 L600,0 Z"/>
      <path fill="var(--brand-dark)" d="M481,0 C510,30 490,120 380,200 C296,259 210,322 158,343 L600,343 L600,0 Z"/>
    </svg>

    <div class="wordmark">
      <span class="wordmark__dot"></span>
      <span class="wordmark__name">BrightNestMums</span>
    </div>

    <div class="contact">
      <p class="contact__name">Lena Forbisher</p>
      <p class="contact__role">Founder</p>
      <p class="contact__line">+64 (0)9 571 4860
        <svg class="contact__icon" viewBox="0 0 14 14"><path fill="var(--brand-light)" d="M3,1 L5,1 L6,4 L4.5,5.5 C5.5,7.5 6.5,8.5 8.5,9.5 L10,8 L13,9 L13,11 C13,12 12,13 11,13 C6,13 1,8 1,3 C1,2 2,1 3,1 Z"/></svg>
      </p>
      <p class="contact__line">021 483 517
        <svg class="contact__icon" viewBox="0 0 14 14"><rect x="3.5" y="0.5" width="7" height="13" rx="1.5" fill="none" stroke="var(--brand-light)" stroke-width="1.3"/><rect x="5" y="2.5" width="4" height="8" fill="var(--brand-light)"/></svg>
      </p>
      <p class="contact__line">BrightNestMums.example
        <svg class="contact__icon" viewBox="0 0 14 14"><circle cx="7" cy="7" r="6.3" fill="var(--brand-light)"/><path fill="var(--brand-dark)" d="M4,3 C6,3 7,5 6,6 C5,7 3,6 3,8 C2,7 2,4 4,3 Z M8,8 C10,7 11,9 10,11 C9,11 8,10 8,8 Z"/></svg>
      </p>
      <p class="contact__address">47 Kowhai Terrace, Ellerslie<br>Auckland 1051, New Zealand</p>
    </div>
  </section>

  <section class="card card--back">
    <div class="back-mark">
      <span class="back-mark__dot"></span>
      <span class="back-mark__name">BrightNestMums</span>
    </div>
    <p class="strapline">Tap; Gather; Sorted</p>
  </section>
</body>
</html>
```